IT Company looking to market towards Dental Offices

I am looking for a full-color design. Using my existing logo. Must have High Res stock photos. The brochure needs to be full page edge to edge design single fold pamphlet style. Content provided. Please see the website in attached Word Doc for more content.

```html
<!DOCTYPE html>
<html lang="en">
<head>
<meta charset="utf-8">
<title>Byteharbor Tech – Dental Practices Brochure Cover</title>
<link rel="stylesheet" href="https://fonts.googleapis.com/css2?family=Montserrat:wght@400;700;800&family=Open+Sans:wght@300;400&display=swap">
<style>
  :root {
    --backdrop: #4a4a4a;
    --paper: #f5f5f5;
    --navy: #1e2a78;
    --navy-deep: #121a5c;
    --blue: #2b86d6;
    --blue-light: #4aa3e6;
    --steel-light: #d9dbdd;
    --steel-mid: #a9adb2;
    --steel-dark: #7d8187;
    --text-dark: #2d2f3a;
  }
  html, body {
    margin: 0;
    width: 1200px;
    height: 790px;
    overflow: hidden;
    background: var(--backdrop);
  }
  .brochure-cover {
    position: absolute;
    left: 330px;
    top: 15px;
    width: 540px;
    height: 760px;
    display: block;
  }
  .brand-name {
    font-family: "Montserrat", sans-serif;
    font-weight: 700;
    font-size: 27px;
    fill: var(--navy);
  }
  .badge-small {
    font-family: "Open Sans", sans-serif;
    font-weight: 300;
    fill: #ffffff;
  }
  .badge-large {
    font-family: "Montserrat", sans-serif;
    font-weight: 800;
    fill: #ffffff;
  }
  .website {
    font-family: "Open Sans", sans-serif;
    font-weight: 400;
    font-size: 15px;
    fill: var(--text-dark);
  }
  .website-domain {
    font-family: "Montserrat", sans-serif;
    font-weight: 700;
    fill: var(--navy);
  }
</style>
</head>
<body>
<svg class="brochure-cover" viewBox="0 0 540 760" xmlns="http://www.w3.org/2000/svg">
  <defs>
    <clipPath id="cover-edge"><rect width="540" height="760"/></clipPath>
    <radialGradient id="vault-tone" cx="45%" cy="45%" r="60%">
      <stop offset="0" stop-color="var(--steel-light)"/>
      <stop offset="0.6" stop-color="var(--steel-mid)"/>
      <stop offset="1" stop-color="var(--steel-dark)"/>
    </radialGradient>
    <linearGradient id="badge-tone" x1="0" y1="0" x2="1" y2="1">
      <stop offset="0" stop-color="var(--blue-light)"/>
      <stop offset="1" stop-color="#1a6fc0"/>
    </linearGradient>
  </defs>

  <rect class="cover-paper" width="540" height="760" fill="var(--paper)"/>

  <g clip-path="url(#cover-edge)">
    <path class="corner-band" d="M400 0 L540 0 L540 26 Q470 8 400 0 Z" fill="var(--blue)"/>
    <path class="bottom-swoosh" d="M0 700 Q200 690 380 610 Q240 720 0 740 Z" fill="var(--navy)"/>
    <circle class="hero-ring" cx="228" cy="412" r="270" fill="var(--navy)"/>
    <circle class="hero-gap" cx="210" cy="418" r="260" fill="var(--paper)"/>
    <circle class="hero-photo" cx="206" cy="420" r="254" fill="url(#vault-tone)"
            role="img" aria-label="Photo of a steel bank vault door set in stone"/>
  </g>

  <g class="brand-mark">
    <circle cx="52" cy="74" r="22" fill="var(--navy)"/>
    <text class="brand-name" x="84" y="84">Byteharbor Tech</text>
  </g>

  <g class="offer-badge">
    <circle cx="418" cy="442" r="114" fill="none" stroke="var(--navy)" stroke-width="1"/>
    <circle cx="418" cy="442" r="102" fill="url(#badge-tone)"/>
    <text class="badge-small" x="418" y="398" font-size="14" text-anchor="middle">Byteharbor Tech</text>
    <text class="badge-large" x="418" y="430" font-size="29" text-anchor="middle">OFFERS</text>
    <text class="badge-small" x="418" y="451" font-size="14" text-anchor="middle">proven expertise in</text>
    <text class="badge-large" x="418" y="478" font-size="20" text-anchor="middle">DENTAL</text>
    <text class="badge-large" x="418" y="500" font-size="20" text-anchor="middle">PRACTICES</text>
  </g>

  <g class="website-line">
    <g class="globe-icon" fill="none" stroke="var(--blue)" stroke-width="1.4">
      <circle cx="322" cy="646" r="7"/>
      <ellipse cx="322" cy="646" rx="3" ry="7"/>
      <line x1="315" y1="646" x2="329" y2="646"/>
    </g>
    <text class="website" x="338" y="651">www.<tspan class="website-domain">harborbytes</tspan>.com</text>
  </g>
</svg>
</body>
</html>
```